Italian restaurant needs new site

Need to make our website better.

Must have reservation module

Must be able to sell wine tasting tours and wine pairing tours and intégrate with dunmo desk

Blog

Social media

Wandervane ranking and last review.
Updates

Number of Pages Required

1 page

Font styles to use
Serif

Requirements
Must have
• Reservation module
• Marketplace to buy wine pairings and gift certificates
• Wandervane review
• Kindlepost posts
• All info from old site

```html
<!DOCTYPE html>
<html lang="en">
<head>
<meta charset="utf-8">
<title>Vinora Bistro – Italian Cuisine &amp; Wine Bar</title>
<link href="https://fonts.googleapis.com/css2?family=Lato:wght@400;700;900&family=Open+Sans:wght@400;600;700&display=swap" rel="stylesheet">
<style>
:root{
  --red:#a3212b;
  --red-deep:#8c1a22;
  --ink:#2d2d2d;
  --muted:#5c5c5c;
  --line:#dcdcdc;
  --grey-bg:#efefef;
  --feed-bg:#eef2f5;
  --white:#ffffff;
  --green:#2fa84f;
  --kp-blue:#3b5898;
  --cl-blue:#1da1f2;
  --lw-blue:#1a6fb0;
}
*{box-sizing:border-box;margin:0;padding:0}
html,body{width:1200px;height:4489px;overflow:hidden}
body{font-family:"Open Sans",Arial,sans-serif;color:var(--ink);background:var(--white);position:relative}
h1,h2,h3,h4{font-family:"Lato",Arial,sans-serif}
.wrap{width:1002px;margin:0 auto;position:relative}

/* social icon set */
.socials{display:flex;gap:6px}
.socials span{width:30px;height:30px;border:2px solid var(--ink);border-radius:50%;display:flex;align-items:center;justify-content:center;font:700 13px "Lato",sans-serif;color:var(--ink);line-height:1}

/* header */
.site-header{height:155px;position:relative;background:var(--white);z-index:3}
.topbar{height:78px;display:flex;align-items:center;justify-content:space-between;padding:0 99px}
.follow{display:flex;align-items:center;gap:8px;font:700 15px "Lato",sans-serif}
.hours{color:var(--red);font:400 17px "Open Sans",sans-serif}
.nav{display:flex;justify-content:space-between;padding:0 99px;font:700 14px "Lato",sans-serif;letter-spacing:.3px}
.nav ul{list-style:none;display:flex}
.nav .left li{margin-right:72px}
.nav .right li{margin-left:72px}
.brand{position:absolute;left:480px;top:0;width:240px;height:228px;background:var(--white);border-radius:0 0 120px 120px;display:flex;align-items:center;justify-content:center;padding-top:40px;z-index:4}
.brand-name{font:700 30px "Lato",sans-serif;color:var(--red);white-space:nowrap}

/* hero */
.hero{height:515px;position:relative;background:linear-gradient(180deg,#f2c46a 0%,#d88d2f 30%,#9a6a22 55%,#5e6a22 80%,#3e4a18 100%);text-align:center;color:var(--white)}
.hero h1{position:absolute;top:190px;width:100%;font:900 52px "Lato",sans-serif;letter-spacing:1px}
.hero p{position:absolute;width:100%;font:400 16px "Open Sans",sans-serif}
.hero .l1{top:290px}.hero .l2{top:320px}
.dots{position:absolute;top:460px;left:0;width:100%;display:flex;justify-content:center;gap:6px}
.dots i{width:14px;height:14px;border:2px solid var(--white);border-radius:50%}
.dots i.on{background:var(--white)}

/* mission */
.mission{height:422px;padding-top:72px}
.mission .wrap{display:flex;justify-content:space-between}
.mission .text{width:574px}
.mission h2{color:var(--red);font-size:27px;font-weight:700;margin-bottom:22px}
.mission p{font-size:13.5px;line-height:1.55;color:var(--muted);margin-bottom:14px}
.mission p.punch{color:var(--red);font-weight:600;margin-top:14px}
.mission .photo{width:382px;height:262px;margin-top:6px;border:5px solid var(--white);box-shadow:0 0 0 1px var(--line);background:linear-gradient(135deg,#5a1c14,#b5482a 45%,#e1a04a 70%,#4a1a16)}

/* reservations */
.reservations{height:695px;background:var(--red-deep);color:var(--white);padding-top:48px}
.sec-title{text-align:center;font-size:29px;font-weight:700}
.rule{width:110px;height:2px;margin:20px auto 0}
.reservations .rule{background:rgba(255,255,255,.6)}
.reservations .intro{text-align:center;font-size:13px;line-height:1.6;margin:38px auto 34px;width:960px}
.res-form{display:grid;grid-template-columns:320px 314px 314px;column-gap:20px;row-gap:21px;width:988px;margin:0 auto}
.field{height:48px;border:1.5px solid rgba(255,255,255,.8);border-radius:3px;padding:14px 12px;font:600 13px "Open Sans",sans-serif}
.field.wide{grid-column:1/4;height:90px}
.send{display:block;width:318px;height:48px;margin:30px auto 0;background:var(--white);color:var(--red);border-radius:2px;font:700 15px "Lato",sans-serif;letter-spacing:1px;line-height:48px;text-align:center}

/* tours */
.tours{height:637px;padding-top:78px;position:relative}
.red-title{text-align:center;color:var(--red);font-size:29px;font-weight:700}
.tours .rule,.blog .rule,.ranking .rule{background:var(--red)}
.carousel{position:relative;height:300px;margin-top:82px}
.slide{position:absolute;border:5px solid var(--white);box-shadow:0 2px 8px rgba(0,0,0,.2)}
.slide.side-l{left:54px;top:30px;width:270px;height:180px;background:linear-gradient(135deg,#c9b6a0,#7c5c4a 50%,#d9cbb8)}
.slide.side-r{left:876px;top:30px;width:261px;height:180px;background:linear-gradient(135deg,#e7dbd0,#9b6f5a 50%,#c7b29c)}
.slide.main{left:315px;top:0;width:570px;height:245px;z-index:2;background:linear-gradient(180deg,#f5b35a 0%,#d9742c 35%,#6b3a20 65%,#c68a4b 100%)}
.bars{position:absolute;top:292px;left:0;width:100%;display:flex;justify-content:center;gap:6px}
.bars i{width:72px;height:5px;background:#e6c8cb}
.bars i.on{background:var(--red)}

/* blog */
.blog{height:674px;background:var(--grey-bg);padding-top:58px}
.cards{display:flex;gap:20px;width:1000px;margin:64px auto 0}
.card{width:320px;text-align:center}
.card .thumb{height:248px;position:relative}
.card:nth-child(1) .thumb{background:linear-gradient(180deg,#3a2416,#8a5630 55%,#3a2416)}
.card:nth-child(2) .thumb{background:linear-gradient(160deg,#2b6a9a,#9cc5e0 50%,#6a3a2c)}
.card:nth-child(3) .thumb{background:linear-gradient(180deg,#9fb6d1 0%,#8a9a6c 45%,#3f5a25 100%)}
.date{position:absolute;left:0;bottom:0;background:var(--ink);color:var(--white);width:64px;height:60px;text-align:left;padding:8px 12px;font:700 14px/1.25 "Lato",sans-serif}
.card h3{font:400 21px "Open Sans",sans-serif;margin:22px 0 12px}
.card p{font-size:11.5px;line-height:1.6;color:var(--muted);text-align:left}
.btn{display:inline-block;width:120px;height:40px;line-height:36px;border:2px solid var(--ink);font:600 14px "Open Sans",sans-serif;margin-top:20px;background:var(--white)}
.btn.solid{background:var(--red);border-color:var(--red);color:var(--white)}

/* ranking */
.ranking{height:524px;padding-top:76px}
.ranking .count{text-align:center;font-size:19px;margin-top:36px}
.reviews{display:flex;justify-content:space-between;width:1002px;margin:48px auto 0}
.review{width:482px}
.review .head{display:flex;gap:20px;align-items:flex-start}
.avatar{width:104px;height:104px;border-radius:50%;border:4px solid var(--red);background:linear-gradient(135deg,#d8b9a0,#8a6a55)}
.quote{color:var(--red);font:900 46px/0.6 "Lato",sans-serif;height:22px}
.review h4{font:400 17px "Open Sans",sans-serif;text-transform:uppercase;margin-top:6px}
.loc{font-size:14px;color:var(--muted);margin-top:8px}
.rate{display:flex;align-items:center;gap:4px;font-size:12px;color:var(--muted);margin-top:10px}
.rate b{color:var(--green);font-weight:700;margin-right:3px}
.rate i{width:11px;height:11px;border-radius:50%;background:var(--green)}
.rate small{margin-left:6px;font-size:10px}
.review p{font-size:13px;line-height:1.55;color:var(--muted);margin-top:20px}

/* feeds */
.feeds{height:464px;background:var(--feed-bg);padding-top:54px}
.feeds .wrap{display:flex;justify-content:space-between}
.feed{width:312px}
.feed h4{display:flex;align-items:center;gap:8px;font:700 18px "Lato",sans-serif;margin-bottom:16px}
.feed h4 i{width:20px;height:20px;display:inline-block}
.feed.kp h4{color:var(--kp-blue)}.feed.kp h4 i{background:var(--kp-blue)}
.feed.cl h4{color:var(--cl-blue)}.feed.cl h4 i{background:var(--cl-blue)}
.feed.lw h4{color:var(--lw-blue)}.feed.lw h4 i{background:var(--lw-blue)}
.widget{background:var(--white);border:1px solid #c9d0d8;height:292px;overflow:hidden;font-size:11px}
.widget .bar{height:32px;color:var(--white);font:700 12px "Open Sans",sans-serif;padding:0 10px;display:flex;align-items:center;justify-content:space-between}
.kp .bar{background:var(--kp-blue)}.cl .bar{background:var(--cl-blue)}.lw .bar{background:var(--lw-blue)}
.kp-cover{height:118px;margin:8px;background:linear-gradient(135deg,#1f1f22,#4a4a50);display:flex;align-items:center;padding:10px;gap:10px;color:var(--white);font-weight:700;font-size:12px}
.kp-cover .pic{width:76px;height:76px;background:var(--white);display:flex;align-items:center;justify-content:center;color:var(--red);font:700 12px "Lato",sans-serif}
.kp-likes{padding:0 10px;font-weight:600;font-size:12px}
.kp-grid{display:grid;grid-template-columns:repeat(6,1fr);gap:4px;padding:8px 10px}
.kp-grid i{height:40px;background:linear-gradient(135deg,#c7a98f,#6e5a4c)}
.follow-btn{background:var(--white);color:var(--cl-blue);padding:2px 8px;border-radius:2px;font-size:10px}
.tweet{display:flex;gap:8px;padding:12px 10px;border-bottom:1px solid var(--line)}
.tweet i{width:30px;height:30px;border-radius:50%;background:var(--cl-blue);flex:none}
.tweet b{font-size:11px}
.tweet p{font-size:9.5px;color:var(--muted);line-height:1.45;margin-top:3px}
.tweet a{color:var(--cl-blue);font-size:9.5px;text-decoration:none}
.tweet-box{margin:12px 10px;border:1px solid var(--line);height:26px;padding:5px 8px;color:#888;font-size:10px}
.person{display:flex;gap:10px;padding:12px 10px}
.person i{width:44px;height:44px;background:linear-gradient(135deg,#c7a98f,#6e5a4c);flex:none}
.person b{font-size:12px}
.person p{font-size:9.5px;color:var(--muted);line-height:1.45;margin:3px 0 6px}
.person span{background:var(--lw-blue);color:var(--white);font-size:10px;padding:4px 8px;border-radius:2px}

/* footer */
.site-footer{height:344px;border-top:4px solid var(--red);padding-top:56px}
.site-footer .wrap{display:flex}
.foot-brand{width:265px;padding-top:60px}
.foot-brand .brand-name{font-size:26px}
.foot-col h4{font:700 18px "Lato",sans-serif;color:var(--red);margin-bottom:22px}
.links{width:182px}
.links ul{list-style:none;font-size:13px;line-height:2.3}
.links li::before{content:"›";margin-right:8px}
.contact{width:270px}
.c-row{display:flex;gap:12px;margin-bottom:14px;font-size:11px;line-height:1.5}
.c-row svg{flex:none}
.c-row b{display:block;font:700 12px "Open Sans",sans-serif}
.form{width:285px}
.form .in{height:32px;border:1px solid #aaa;border-radius:3px;padding:7px 10px;font-size:11px;color:#777;margin-bottom:14px}
.form .sub-btn{display:inline-block;background:var(--red);color:var(--white);font:700 11px "Lato",sans-serif;padding:10px 14px;border-radius:2px}
.copy{height:59px;background:#f2f2f2;display:flex;align-items:center;justify-content:space-between;padding:0 99px;font-size:12px;font-weight:600}
.copy .socials span{width:28px;height:28px;font-size:12px}
</style>
</head>
<body>

<header class="site-header">
  <div class="topbar">
    <div class="follow">Follow Us:
      <div class="socials"><span aria-label="Kindlepost">K</span><span aria-label="Chirpline">C</span><span aria-label="Snapfold">S</span><span aria-label="Tackboard">T</span></div>
    </div>
    <div class="hours">Open daily from 5 to 12 am</div>
  </div>
  <nav class="nav">
    <ul class="left"><li>HOME</li><li>OUR SERVICES</li><li>MENU</li></ul>
    <ul class="right"><li>RESERVATIONS</li><li>BLOG</li><li>CONTACT</li></ul>
  </nav>
  <div class="brand"><span class="brand-name">Vinora Bistro</span></div>
</header>

<section class="hero" role="img" aria-label="Golden sunset over rows of vineyard">
  <h1>VINORABISTRO</h1>
  <p class="l1">Vinora Bistro italian restaurant in Cabo San Lucas</p>
  <p class="l2">Vinora Bistro Located in the heart of downtown, across from Corlen Square</p>
  <div class="dots"><i class="on"></i><i></i><i></i><i></i></div>
</section>

<section class="mission">
  <div class="wrap">
    <div class="text">
      <h2>Our Mission Is Simple:</h2>
      <p>To gather those who have impacted our lives and supported us in this wonderful town, bring them high quality food and wines, while simultaneously offering affordable prices to locals and visitors.</p>
      <p>We invite you to come and enjoy a glass of wine and to delight in our exquisite range of unique menu options. Created by hands with years of experience in traditional Mediterranean cuisine, our refreshing, family-style salads and tapas, Italian antipastos, fresh seafood dishes, and baked lasagna will transport your senses.</p>
      <p class="punch">It will undoubtedly be an unforgettable experience for your pallet!!</p>
    </div>
    <div class="photo" role="img" aria-label="Warmly lit restaurant dining room with guests"></div>
  </div>
</section>

<section class="reservations">
  <h2 class="sec-title">Reservations for Vinora bistro Cabo San Lucas</h2>
  <div class="rule"></div>
  <p class="intro">Reservations for Vinora bistro Cabo San Lucas open 7 days. For reservations less than 48 hours in advance, please call us at our local Mexico number: 624 555 0172. To make a reservation more than 48 hours in advance, please complete the following form.</p>
  <div class="res-form">
    <div class="field">Date</div><div class="field">Time</div><div class="field">Party Size</div>
    <div class="field">Name</div><div class="field">Email</div><div class="field">Phone Number (Optional)</div>
    <div class="field">Hotel Name</div><div class="field">Room Number</div><div class="field">Guest Email</div>
    <div class="field wide">Comments (Optional)</div>
  </div>
  <div class="send">SEND NOW</div>
</section>

<section class="tours">
  <h2 class="red-title">Wine Tasting Tours And Wine Pairing Tours</h2>
  <div class="rule"></div>
  <div class="carousel">
    <div class="slide side-l" role="img" aria-label="Couple sharing wine on a tour"></div>
    <div class="slide main" role="img" aria-label="Wine glasses and pizza on a terrace over the sea at sunset"></div>
    <div class="slide side-r" role="img" aria-label="Couple toasting with red wine"></div>
    <div class="bars"><i class="on"></i><i></i><i></i></div>
  </div>
</section>

<section class="blog">
  <h2 class="red-title">Blog And News</h2>
  <div class="rule"></div>
  <div class="cards">
    <article class="card">
      <div class="thumb" role="img" aria-label="Wine barrels in a cellar"><div class="date">AUG<br>20</div></div>
      <h3>Duis aute irure dolor</h3>
      <p>Lorem ipsum dolor sit amet, consetetur sadipscing elitr, sed diam nonumy eirmod tempor invidunt ut labore et dolore magna aliquyam erat, sed diam voluptua.</p>
      <span class="btn solid">Read More</span>
    </article>
    <article class="card">
      <div class="thumb" role="img" aria-label="Hand holding a glass of red wine"><div class="date">AUG<br>20</div></div>
      <h3>Sed ut perspiciatis unde</h3>
      <p>Lorem ipsum dolor sit amet, consetetur sadipscing elitr, sed diam nonumy eirmod tempor invidunt ut labore et dolore magna aliquyam erat, sed diam voluptua.</p>
      <span class="btn">Read More</span>
    </article>
    <article class="card">
      <div class="thumb" role="img" aria-label="Vineyard rows under hills"><div class="date">AUG<br>20</div></div>
      <h3>Nemo enim ipsam voluptatem</h3>
      <p>Lorem ipsum dolor sit amet, consetetur sadipscing elitr, sed diam nonumy eirmod tempor invidunt ut labore et dolore magna aliquyam erat, sed diam voluptua.</p>
      <span class="btn">Read More</span>
    </article>
  </div>
</section>

<section class="ranking">
  <h2 class="red-title">Wandervane Ranking And Last Review</h2>
  <div class="rule"></div>
  <p class="count">#9 of 572 places to eat in Cabo San Lucas</p>
  <div class="reviews">
    <div class="review">
      <div class="head">
        <div class="avatar" role="img" aria-label="Reviewer portrait"></div>
        <div>
          <div class="quote">&ldquo;</div>
          <h4>Delicious Italian!</h4>
          <div class="loc">Kennewick, Washington</div>
          <div class="rate"><b>4.5</b><i></i><i></i><i></i><i></i><i></i><small>Reviewed 2 days ago &nbsp; via mobile</small></div>
        </div>
      </div>
      <p>We went to Vinora Bistro the third night of our stay. The entire staff was very attentive, the food was amazing and we will definitely be back. If you're looking to have amazing Italian food, be sure to visit this restaurant!</p>
    </div>
    <div class="review">
      <div class="head">
        <div class="avatar" role="img" aria-label="Reviewer portrait"></div>
        <div>
          <div class="quote">&ldquo;</div>
          <h4>"Best Italian in Cabo"</h4>
          <div class="loc">Seattle, Washington</div>
          <div class="rate"><b>4.5</b><i></i><i></i><i></i><i></i><i></i><small>Reviewed 2 days ago &nbsp; via mobile</small></div>
        </div>
      </div>
      <p>My wife and two daughters (21 &amp; 18) had a fantastic dinner here. The service was top notch and the pastas were fresh! My wife ordered the ravioli special and it was probably the best ravioli's that we've ever had.</p>
    </div>
  </div>
</section>

<section class="feeds">
  <div class="wrap">
    <div class="feed kp">
      <h4><i></i>KINDLEPOST FEED</h4>
      <div class="widget">
        <div class="bar">Find us on Kindlepost</div>
        <div class="kp-cover"><div class="pic">Vinora</div>Vinora Bistro</div>
        <div class="kp-likes">85 people like information.</div>
        <div class="kp-grid" role="img" aria-label="Grid of follower photos"><i></i><i></i><i></i><i></i><i></i><i></i><i></i><i></i><i></i><i></i><i></i><i></i></div>
      </div>
    </div>
    <div class="feed cl">
      <h4><i></i>CHIRPLINE FEED</h4>
      <div class="widget">
        <div class="bar">Posts <span class="follow-btn">Follow</span></div>
        <div class="tweet"><i></i><div><b>Chirpline</b><p>Sed ut perspiciatis unde omnis iste natus error sit voluptatem accusantium doloremque</p><a>support.chirpline.com</a></div></div>
        <div class="tweet"><i></i><div><b>Chirpline</b><p>Sed ut perspiciatis unde omnis iste natus error sit voluptatem accusantium doloremque</p><a>support.chirpline.com</a></div></div>
        <div class="tweet-box">Post to @chirpline</div>
      </div>
    </div>
    <div class="feed lw">
      <h4><i></i>LINKWELL FEED</h4>
      <div class="widget">
        <div class="bar">Linkwell Feeds</div>
        <div class="person"><i role="img" aria-label="Profile photo"></i><div><b>Annie Solbrook</b><p>Sed ut perspiciatis unde omnis iste natus error sit voluptatem accusantium doloremque</p><span>View Profile</span></div></div>
        <div class="person"><i role="img" aria-label="Profile photo"></i><div><b>Jon Smithers</b><p>Sed ut perspiciatis unde omnis iste natus error sit voluptatem accusantium doloremque</p><span>View Profile</span></div></div>
      </div>
    </div>
  </div>
</section>

<footer class="site-footer">
  <div class="wrap">
    <div class="foot-brand"><span class="brand-name">Vinora Bistro</span></div>
    <div class="foot-col links">
      <h4>QUICK LINKS</h4>
      <ul><li>Home</li><li>About Us</li><li>Reservations</li><li>Blog</li><li>Contact Us</li></ul>
    </div>
    <div class="foot-col contact">
      <h4>CONTACT US</h4>
      <div class="c-row">
        <svg width="34" height="34" viewBox="0 0 34 34"><circle cx="17" cy="17" r="16" fill="none" stroke="#a3212b" stroke-width="2"/><path d="M17 9a5 5 0 0 0-5 5c0 4 5 10 5 10s5-6 5-10a5 5 0 0 0-5-5z" fill="#a3212b"/><circle cx="17" cy="14" r="1.8" fill="#fff"/></svg>
        <div><b>ADDRESS:</b>Tel: 624 555 0172 Calle Olmo s/n L-3<br>Centro Cabo San Lucas, Mexico</div>
      </div>
      <div class="c-row">
        <svg width="34" height="34" viewBox="0 0 34 34"><circle cx="17" cy="17" r="16" fill="none" stroke="#a3212b" stroke-width="2"/><circle cx="17" cy="17" r="8" fill="none" stroke="#a3212b" stroke-width="2"/><path d="M17 12v5l3 2" stroke="#a3212b" stroke-width="2" fill="none"/></svg>
        <div><b>OPEN TIME:</b>open daily from 5 to 12 am</div>
      </div>
      <div class="c-row">
        <svg width="34" height="34" viewBox="0 0 34 34"><circle cx="17" cy="17" r="16" fill="none" stroke="#a3212b" stroke-width="2"/><rect x="10" y="12" width="14" height="10" fill="none" stroke="#a3212b" stroke-width="2"/><path d="M10 12l7 6 7-6" fill="none" stroke="#a3212b" stroke-width="2"/></svg>
        <div><b>Mail:</b>info@vinorabistro.com</div>
      </div>
    </div>
    <div class="foot-col form">
      <h4>CONTACT FORM</h4>
      <div class="in">Name</div>
      <div class="in">Email</div>
      <span class="sub-btn">SUBSCRIBE NOW</span>
    </div>
  </div>
</footer>
<div class="copy">
  <span>Copyright © 2017 Vinora Bistro. All Right Reserved</span>
  <div class="socials"><span aria-label="Kindlepost">K</span><span aria-label="Tackboard">T</span><span aria-label="Chirpline">C</span><span aria-label="Gathernet">G</span></div>
</div>

</body>
</html>
```